MRT Property - Business Cards

Looking for a business card & general letterhead, signage etc design for our new logo.

Colours:
000a20
0056a2
00b5ef
0088ce
68cef2

Fonts:
Poppins
Karla

Please keep look and feel of new brand - example in the zip package I sent.

```html
<!DOCTYPE html>
<html lang="en">
<head>
<meta charset="utf-8">
<title>MRT Property – Business Cards</title>
<link rel="stylesheet" href="https://fonts.googleapis.com/css2?family=Karla:wght@400;500&family=Poppins:wght@700&display=swap">
<style>
  :root {
    --ink: #000a20;
    --brand-blue: #0056a2;
    --bright-cyan: #00b5ef;
    --mid-blue: #0088ce;
    --sky: #68cef2;
    --paper: #ffffff;
    --muted: #6b7280;
    --stage: #11161f;
  }
  * { box-sizing: border-box; margin: 0; padding: 0; }
  html, body { width: 1200px; height: 963px; overflow: hidden; }
  body {
    background: var(--stage);
    font-family: "Karla", sans-serif;
    position: relative;
  }
  .card {
    position: absolute;
    left: 280px;
    width: 640px;
    height: 366px;
    border-radius: 22px;
    overflow: hidden;
  }
  .card--front { top: 90px; background: var(--paper); }
  .card--back { top: 507px; background: var(--brand-blue); display: flex; align-items: center; justify-content: center; }
  .card__wave { position: absolute; inset: 0; width: 100%; height: 100%; }

  .brand {
    display: flex;
    align-items: center;
    gap: 14px;
    font-family: "Poppins", sans-serif;
    font-weight: 700;
    letter-spacing: 0.5px;
  }
  .brand__dot { border-radius: 50%; flex: none; }
  .card--front .brand { position: absolute; left: 170px; top: 56px; color: var(--brand-blue); font-size: 46px; }
  .card--front .brand__dot { width: 30px; height: 30px; background: var(--brand-blue); }
  .card--back .brand { color: var(--paper); font-size: 62px; }
  .card--back .brand__dot { width: 40px; height: 40px; background: var(--paper); }

  .address {
    position: absolute; left: 70px; top: 136px;
    color: var(--muted); font-size: 17px; line-height: 1.3;
  }
  .person {
    position: absolute; right: 44px; top: 148px; text-align: right;
  }
  .person__name {
    font-family: "Poppins", sans-serif; font-weight: 700;
    color: var(--bright-cyan); font-size: 21px; letter-spacing: 0.5px; text-transform: uppercase;
  }
  .person__role { color: var(--muted); font-size: 17px; }

  .contact {
    position: absolute; right: 40px; bottom: 20px;
    list-style: none; color: var(--paper); font-size: 18px; line-height: 1.45; text-align: right;
  }
  .contact li { display: flex; align-items: center; justify-content: flex-end; gap: 10px; }
  .contact svg { width: 16px; height: 16px; flex: none; }
</style>
</head>
<body>
  <section class="card card--front" aria-label="Business card front">
    <svg class="card__wave" viewBox="0 0 640 366" aria-hidden="true">
      <path d="M0,185 C100,270 300,255 440,245 C540,238 600,245 640,255 L640,366 L0,366 Z" fill="var(--brand-blue)"/>
      <path d="M0,174 C100,258 300,244 440,234 C540,227 600,235 640,244" fill="none" stroke="var(--paper)" stroke-width="8"/>
      <path d="M30,182 C120,240 230,240 300,238" fill="none" stroke="var(--mid-blue)" stroke-width="6"/>
      <path d="M100,196 C210,228 330,222 450,216 C540,212 600,222 640,232" fill="none" stroke="var(--sky)" stroke-width="7"/>
    </svg>

    <div class="brand"><span class="brand__dot"></span>MRT Property</div>

    <p class="address">Your Address, City<br>State, Zip 0000</p>

    <div class="person">
      <p class="person__name">Daniel Harper</p>
      <p class="person__role">Manager</p>
    </div>

    <ul class="contact">
      <li>123-456-2100
        <svg viewBox="0 0 16 16"><path d="M4 1.5 L6 4.5 L4.6 6 C5.4 8 7.8 10.4 10 11.4 L11.5 10 L14.5 12 L13 14.5 C7 14 2 9 1.5 3 Z" fill="var(--paper)"/></svg>
      </li>
      <li>youremail@mailbox.com
        <svg viewBox="0 0 16 16"><rect x="1.5" y="3.5" width="13" height="9" rx="1" fill="none" stroke="var(--paper)" stroke-width="1.4"/><path d="M1.5 4 L8 9 L14.5 4" fill="none" stroke="var(--paper)" stroke-width="1.4"/></svg>
      </li>
      <li>www.yourwebsite.com
        <svg viewBox="0 0 16 16"><circle cx="8" cy="8" r="6.5" fill="none" stroke="var(--paper)" stroke-width="1.4"/><ellipse cx="8" cy="8" rx="3" ry="6.5" fill="none" stroke="var(--paper)" stroke-width="1.2"/><path d="M1.5 8 H14.5 M2.5 5 H13.5 M2.5 11 H13.5" stroke="var(--paper)" stroke-width="1.1"/></svg>
      </li>
    </ul>
  </section>

  <section class="card card--back" aria-label="Business card back">
    <div class="brand"><span class="brand__dot"></span>MRT Property</div>
  </section>
</body>
</html>
```